body balm label design

body balm tube design, current label design for other similar products
Need to have a design which can interchange between 3 different solutions
Amber Tide (Lavender + Vanilla)
Copper Ridge (Eucalyptus + Mint)
Fern Hollow (Bergamot + Cedarwood)
Tube size:
2.5h x 3.25 w
Target Market(s)
natural, solution focused
Requirements
Must have
- relatable to existing brand designs, focus on features and benefits

```html
<!DOCTYPE html>
<html lang="en">
<head>
<meta charset="utf-8">
<title>Amber Tide Natural Body Balm Label</title>
<link rel="stylesheet" href="https://fonts.googleapis.com/css2?family=Cormorant+Garamond:wght@500&family=Raleway:wght@300&family=Quicksand:wght@300;400;700&family=Sacramento&family=Cormorant:wght@500&display=swap">
<style>
  :root {
    --slate: #8a9ba6;
    --slate-soft: #a3b0b8;
    --mist: #e6ebee;
    --paper: #ffffff;
  }
  html, body {
    margin: 0;
    padding: 0;
    width: 1200px;
    height: 923px;
    overflow: hidden;
    background: var(--paper);
  }
  .label {
    position: relative;
    width: 1200px;
    height: 923px;
    background: var(--paper);
    overflow: hidden;
    font-family: "Quicksand", sans-serif;
    color: var(--slate);
  }
  .label-art {
    position: absolute;
    inset: 0;
  }
  .info {
    position: absolute;
    left: 956px;
    top: 150px;
    width: 230px;
    font-size: 17.5px;
    font-weight: 300;
    letter-spacing: 1.4px;
    line-height: 24.6px;
  }
  .info h2 {
    margin: 0 0 8px;
    font-size: 17px;
    font-weight: 700;
    letter-spacing: 2px;
  }
  .info p {
    margin: 0 0 22px;
  }
  .social {
    position: absolute;
    left: 958px;
    top: 748px;
    display: flex;
    gap: 14px;
  }
  .social span {
    width: 40px;
    height: 40px;
    border-radius: 50%;
    background: var(--slate);
  }
  .maker {
    position: absolute;
    left: 908px;
    top: 806px;
    width: 240px;
    text-align: center;
    font-size: 18px;
    font-weight: 400;
    letter-spacing: 1.6px;
  }
  .site {
    position: absolute;
    left: 908px;
    top: 838px;
    width: 240px;
    text-align: center;
    font-size: 15px;
    font-weight: 700;
    letter-spacing: 2.4px;
  }
  .net-weight {
    position: absolute;
    left: 90px;
    top: 812px;
    font-family: "Raleway", sans-serif;
    font-weight: 300;
    font-size: 27px;
    line-height: 36px;
    letter-spacing: 0.5px;
    color: var(--slate-soft);
  }
</style>
</head>
<body>
<main class="label">
  <svg class="label-art" width="1200" height="923" viewBox="0 0 1200 923" xmlns="http://www.w3.org/2000/svg">
    <defs>
      <radialGradient id="floral-wash" cx="50%" cy="50%" r="55%">
        <stop offset="0%" stop-color="#e9eef1"/>
        <stop offset="70%" stop-color="#f2f5f6"/>
        <stop offset="100%" stop-color="#ffffff"/>
      </radialGradient>
      <path id="badge-arc" d="M 128 742 A 60 60 0 1 1 206 636"/>
    </defs>

    <rect class="floral-illustration" x="40" y="30" width="830" height="840" rx="300" fill="url(#floral-wash)" role="img" aria-label="Fine line drawing of vanilla orchid blossoms and long leaves"/>

    <!-- product name -->
    <text class="product-name" transform="translate(450 655) rotate(-90)" textLength="585" lengthAdjust="spacingAndGlyphs" font-family="Cormorant Garamond, serif" font-weight="500" font-size="160" fill="var(--slate)">AMBER</text>
    <text class="product-name-script" transform="translate(512 258) rotate(-90)" font-family="Sacramento, cursive" font-size="64" fill="var(--slate)">tide</text>

    <line class="divider" x1="492" y1="258" x2="492" y2="923" stroke="var(--slate)" stroke-width="4"/>

    <!-- tube band -->
    <path class="band" d="M536 923 V150 A88 88 0 0 1 712 150 V923 Z" fill="var(--slate)"/>
    <circle class="brand-dot" cx="624" cy="118" r="6" fill="var(--paper)"/>
    <text class="brand-name" x="624" y="160" text-anchor="middle" font-family="Cormorant Garamond, serif" font-weight="500" font-size="20" letter-spacing="3" fill="var(--paper)">WILLOW BAY</text>
    <text class="band-title" transform="translate(612 325) rotate(-90)" text-anchor="end" font-family="Raleway, sans-serif" font-weight="300" font-size="52" letter-spacing="2" fill="var(--paper)">NATURAL</text>
    <text class="band-title" transform="translate(690 325) rotate(-90)" text-anchor="end" font-family="Raleway, sans-serif" font-weight="300" font-size="52" letter-spacing="2" fill="var(--paper)">BODY BALM</text>

    <!-- scent -->
    <text class="scent" transform="translate(836 658) rotate(-90)" textLength="575" lengthAdjust="spacingAndGlyphs" font-family="Sacramento, cursive" font-size="100" fill="var(--slate)">Lavender + Vanilla</text>

    <!-- origin badge -->
    <text class="badge-arc" font-family="Cormorant, serif" font-weight="500" font-size="25" fill="var(--slate)"><textPath href="#badge-arc">Made In Canada</textPath></text>
    <text class="badge-figure" x="168" y="668" text-anchor="middle" font-family="Cormorant, serif" font-weight="500" font-size="26" fill="var(--slate)">100%</text>
    <text class="badge-word" x="168" y="692" text-anchor="middle" font-family="Cormorant, serif" font-weight="500" font-size="15" fill="var(--slate)">NATURAL</text>
  </svg>

  <section class="info">
    <h2>Ingredients:</h2>
    <p>Shea butter,<br>cocoa butter,<br>coconut oil,<br>sweet almond oil,<br>beeswax,<br>lavender<br>essential oil,<br>vanilla extract or<br>vanilla oleoresin,<br>vitamin E oil</p>
    <h2>How to use:</h2>
    <p>Gently push the<br>balm up from the<br>bottom of the<br>tube using your<br>finger,&nbsp; apply it<br>directly to your<br>skin.</p>
  </section>

  <div class="social" aria-hidden="true"><span></span><span></span><span></span></div>
  <div class="maker">Made by Willow Bay</div>
  <div class="site">WWW.WILLOWBAY.CA</div>

  <div class="net-weight">NET WT 4 oz<br>/120g</div>
</main>
</body>
</html>
```